Veldmark Supplies Business Card

Professional business card that stand out to our potential customers. Front and back with clean modern design

Industry/Entity Type

Oil and gas

Contact Information for Business Card

Name, address, website , office phone and cell number

Requirements
Must have
• Editable files for each employee

```html
<!DOCTYPE html>
<html lang="en">
<head>
<meta charset="utf-8">
<title>Veldmark Supplies – Business Card</title>
<link href="https://fonts.googleapis.com/css2?family=Poppins:wght@400;600;700&display=swap" rel="stylesheet">
<style>
  :root {
    --brand-red: #e82127;
    --brand-blue: #14b1d2;
    --ink: #1d1d1f;
    --paper: #ffffff;
    --backdrop: #e3e7e9;
    --peach: #f3c6a6;
  }
  * { box-sizing: border-box; margin: 0; padding: 0; }
  html, body {
    width: 1200px; height: 960px; overflow: hidden;
    background: var(--backdrop);
    font-family: "Poppins", sans-serif;
  }
  .card {
    position: absolute; left: 268px; width: 664px; height: 379px;
    overflow: hidden; background: var(--paper);
  }
  .card-front { top: 82px; }
  .card-back { top: 499px; }

  .monogram-pattern {
    position: absolute; inset: 0;
    background:
      radial-gradient(ellipse at 92% 12%, var(--peach) 0%, rgba(243,198,166,0.55) 28%, rgba(232,33,39,0) 60%),
      var(--brand-red);
  }

  .brand-lockup {
    position: absolute; left: 30px; top: 164px; width: 260px;
    display: flex; align-items: center; justify-content: center; gap: 10px;
  }
  .brand-square { width: 18px; height: 18px; background: var(--brand-red); }
  .brand-name {
    font-weight: 600; font-size: 22px; color: var(--brand-red);
    letter-spacing: 0.5px;
  }

  .divider {
    position: absolute; left: 331px; top: 72px; width: 1px; height: 234px;
    background: var(--brand-red);
  }

  .person { position: absolute; left: 380px; top: 106px; }
  .person-name { font-size: 28px; line-height: 1; white-space: nowrap; }
  .person-name .first { font-weight: 700; color: var(--brand-red); }
  .person-name .last { font-weight: 400; color: var(--brand-blue); }
  .person-role { margin-top: 8px; font-size: 16px; font-weight: 400; color: var(--ink); }

  .contact-list { position: absolute; left: 381px; top: 186px; list-style: none; }
  .contact-list li {
    display: flex; align-items: center; gap: 9px;
    height: 22px; font-size: 16px; color: var(--ink); white-space: nowrap;
  }
  .contact-list svg { width: 15px; height: 15px; flex: none; }

  .address {
    position: absolute; left: 0; right: 0; top: 322px;
    text-align: center; font-size: 15px; color: var(--brand-red);
  }
  .footer-band { position: absolute; left: 0; bottom: 0; width: 664px; height: 24px; }
</style>
</head>
<body>

<section class="card card-front">
  <div class="monogram-pattern" role="img" aria-label="Repeating brand monogram pattern on red, fading to peach at the upper right"></div>
</section>

<section class="card card-back">
  <div class="brand-lockup">
    <span class="brand-square"></span>
    <span class="brand-name">Veldmark Supplies</span>
  </div>

  <div class="divider"></div>

  <div class="person">
    <h1 class="person-name"><span class="first">Lenka</span> <span class="last">Marova</span></h1>
    <p class="person-role">Co-Founder &amp; CEO</p>
  </div>

  <ul class="contact-list">
    <li>
      <svg viewBox="0 0 16 16" aria-hidden="true"><path d="M4 1.5l2.2 3-1.3 1.6c.9 2 2.4 3.6 4.4 4.5l1.6-1.3 3 2.2-1.4 2.6C6.8 14 2 9.2 1.4 3z" fill="none" stroke="var(--brand-blue)" stroke-width="1.5" stroke-linejoin="round"/></svg>
      (817) 555-0143
    </li>
    <li>
      <svg viewBox="0 0 16 16" aria-hidden="true"><rect x="4" y="1" width="8" height="14" rx="1.2" fill="none" stroke="var(--brand-red)" stroke-width="1.5"/></svg>
      (817) 555-0187
    </li>
    <li>
      <svg viewBox="0 0 16 16" aria-hidden="true"><circle cx="8" cy="8" r="7" fill="var(--brand-blue)"/><path d="M3 5c2 0 3 1 2.5 3S7 10 6 13M10 2.5c-1 2 1 3 3 3M11 10c1 0 2 .5 2.5 1.5" fill="none" stroke="#fff" stroke-width="1.1"/></svg>
      www.veldmarksupply.com
    </li>
    <li>
      <svg viewBox="0 0 16 16" aria-hidden="true"><path d="M1.5 6.5L8 2l6.5 4.5V14.5h-13z" fill="none" stroke="var(--brand-red)" stroke-width="1.4" stroke-linejoin="round"/><path d="M1.5 6.5L8 11l6.5-4.5" fill="none" stroke="var(--brand-red)" stroke-width="1.4"/></svg>
      hello@veldmarksupply.com
    </li>
  </ul>

  <p class="address">1840 Crestline Ave. Suite 310 Fort Worth, TX 76104</p>

  <svg class="footer-band" viewBox="0 0 664 24" preserveAspectRatio="none" aria-hidden="true">
    <rect x="0" y="0" width="664" height="24" fill="var(--paper)"/>
    <polygon points="0,0 304,0 280,24 0,24" fill="var(--brand-red)"/>
    <polygon points="314,0 332,0 308,24 290,24" fill="var(--brand-blue)"/>
    <polygon points="342,0 372,0 348,24 318,24" fill="var(--brand-red)"/>
    <polygon points="382,0 664,0 664,24 358,24" fill="var(--brand-blue)"/>
  </svg>
</section>

</body>
</html>
```